Lumora Systems New Website - IT Infrastructure | Smart Cabinet | Micro Data Center

We're an IT SI providing Server Room Design & Build | All-in-One Rack & Smart Cabinet | Structured Cabling | IT Relocation | Maintenance. Old website can be found at www.lumorasys.com.hk. We'd like a brand new wix website which is modern, minimalist, interactive with some animation. Website content will be mostly static and include our service, our project, news and events, about us, contacts, blogs, partners and brands, etc.

reference sites:
We'd like to see more designs referring to below

https://www.pixelvane.example/design/41736205
https://www.pixelvane.example/design/41892417
https://velbrinn.example/

Animation (scrolling effect) referring to
https://velbrinn.example/intelligence/smart-office-room/
Updates

we'd like below style.

Designs look the same

Target Market(s)

Commercials in HK

Industry/Entity Type

IT, Technology, Data Center

Coding

Coded - Design and coding required

Font styles to use
Sans Serif

Requirements
Must have
• CMS, Some Interactive Elements/ Graphics

```html
<!DOCTYPE html>
<html lang="en">
<head>
<meta charset="utf-8">
<title>Lumora Systems — IT Infrastructure | Smart Cabinet | Micro Data Center</title>
<link href="https://fonts.googleapis.com/css2?family=Merriweather:wght@400;700;900&family=Montserrat:wght@500;600&display=swap" rel="stylesheet">
<style>
:root{
  --navy:#0f1a3a;
  --navy-deep:#0b1230;
  --ink:#0c1128;
  --red:#d2391f;
  --red-event:#d23a22;
  --white:#ffffff;
  --grey:#8a8f99;
  --line:#c9ccd2;
  --footer:#0a0e1a;
}
*{margin:0;padding:0;box-sizing:border-box}
html,body{width:1200px;height:5208px;overflow:hidden}
body{position:relative;font-family:"Merriweather",serif;color:var(--ink);background:var(--white)}
.abs{position:absolute}
.section{position:absolute;left:0;width:1200px}
.heading{position:absolute;left:0;width:1200px;text-align:center;font-weight:900;font-size:38px;letter-spacing:.5px;color:var(--ink)}
.heading .accent{color:var(--red)}
.heading .mark{display:inline-block;width:30px;height:30px;border:4px solid var(--red);margin-left:20px;vertical-align:-2px}
.heading.light{color:var(--white)}
.heading.light .mark{border-color:var(--white)}

/* nav */
.topbar{top:0;height:84px;background:var(--navy)}
.brand{position:absolute;display:flex;align-items:center;gap:10px;color:var(--white);font-family:"Merriweather",serif;font-weight:700;font-size:28px}
.brand .sq{width:30px;height:30px;border:3px solid var(--white)}
.nav{position:absolute;top:34px;left:465px;display:flex;gap:0;font-family:"Montserrat",sans-serif;font-weight:600;font-size:14px;letter-spacing:1px;color:var(--white)}
.nav span{position:absolute;white-space:nowrap}

/* hero */
.hero{top:84px;height:546px;background:linear-gradient(100deg,#0b1634 0%,#142a55 45%,#0e1d40 70%,#1b2f5a 100%)}
.hero h1{position:absolute;left:128px;top:176px;color:var(--white);font-weight:900;font-size:40px;line-height:58px}

/* services */
.services{top:630px;height:540px}
.svc{position:absolute;top:240px;width:190px;height:190px}
.svc svg{position:absolute;left:-10px;top:-10px}
.svc .label{position:absolute;left:0;top:60px;width:180px;text-align:center;font-size:16px;line-height:27px;color:var(--ink)}
.svc .icon{position:absolute;left:55px;top:-76px;width:76px;height:76px;border-radius:50%;background:var(--red);box-shadow:0 0 0 8px #f1f1f1}

/* about */
.about{top:1170px;height:482px;background:var(--navy)}
.about .photo{position:absolute;left:600px;top:0;width:600px;height:482px;background:linear-gradient(90deg,var(--navy) 0%,#13305a 25%,#1f5f86 60%,#0f2a4c 100%)}
.about h2{position:absolute;left:120px;top:42px;color:var(--white);font-weight:900;font-size:38px;line-height:60px}
.about h2 .mark{display:inline-block;width:32px;height:32px;border:4px solid var(--white);margin-left:18px;vertical-align:-4px}
.about p{position:absolute;left:126px;top:176px;width:440px;color:var(--white);font-size:14px;line-height:34px}
.btn-outline{position:absolute;left:126px;top:378px;width:176px;height:58px}
.btn-outline .back{position:absolute;left:12px;top:12px;width:176px;height:58px;border:3px solid var(--white)}
.btn-outline .front{position:absolute;left:0;top:0;width:176px;height:58px;background:var(--white);color:var(--ink);font-weight:700;font-size:18px;display:flex;align-items:center;justify-content:center;letter-spacing:.5px}

/* projects */
.projects{top:1652px;height:700px}
.proj{position:absolute;top:190px;width:263px;height:356px}
.proj .cap{position:absolute;top:380px;left:-40px;width:343px;text-align:center;font-size:16px;line-height:34px}

/* partners */
.partners{top:2352px;height:390px;background:var(--navy-deep)}
.badge{position:absolute;height:42px;background:var(--white);border-radius:2px}
.dot{position:absolute;top:354px;width:12px;height:12px;border-radius:50%;background:var(--white)}

/* blog */
.blog{top:2742px;height:600px}
.post{position:absolute;top:194px;width:297px;height:334px;background:var(--white);box-shadow:0 2px 8px rgba(0,0,0,.18)}
.post .img{width:297px;height:150px}
.post .date{position:absolute;left:24px;top:170px;font-size:11px;color:var(--red)}
.post h3{position:absolute;left:24px;top:196px;width:255px;font-size:13px;line-height:25px;font-weight:700}
.post .ex{position:absolute;left:24px;top:256px;width:255px;font-size:9px;line-height:17px;color:#444}
.post .more{position:absolute;left:26px;top:304px;font-size:10px;font-weight:700;color:var(--red);letter-spacing:.3px}

/* events */
.events{top:3342px;height:618px;background:var(--red-event)}
.tabs{position:absolute;left:138px;top:126px;width:418px;height:62px;border:3px solid var(--white);display:flex}
.tabs div{flex:1;display:flex;align-items:center;justify-content:center;font-size:14px;font-weight:700;color:var(--white)}
.tabs .on{background:var(--navy)}
.ev{position:absolute;left:120px;width:480px;color:var(--white)}
.ev .d{position:absolute;left:0;width:52px;text-align:center;font-size:18px;line-height:25px}
.ev .t{position:absolute;left:68px;width:470px;font-size:12px;line-height:25px}
.events .photo{position:absolute;left:603px;top:130px;width:597px;height:488px;background:linear-gradient(160deg,#1a1450 0%,#2a3f9e 40%,#1976c9 65%,#c23a8a 100%)}

/* contact */
.contact{top:3960px;height:800px;background:linear-gradient(180deg,#ffffff 0%,#ffffff 42%,#d8e3ea 58%,#5f8299 78%,#14344c 100%)}
.field{position:absolute;width:245px;height:48px;border:1.5px solid #7d8088;background:var(--white);font-size:13px;color:#555;padding:14px 14px}
.submit{position:absolute;left:513px;top:460px;width:167px;height:50px}
.submit .back{position:absolute;left:12px;top:8px;width:167px;height:50px;border:3px solid var(--red)}
.submit .front{position:absolute;left:0;top:0;width:167px;height:50px;background:var(--navy);color:var(--white);font-weight:700;font-size:17px;display:flex;align-items:center;justify-content:center}

/* footer */
.footer{top:4760px;height:448px;background:var(--footer);color:var(--white)}
.footer h4{position:absolute;font-size:14px;font-weight:700}
.footer .links{position:absolute;left:327px;top:72px;font-size:12px;line-height:33px}
.crow{position:absolute;left:496px;font-size:13px;line-height:25px}
.crow svg{position:absolute;left:0;top:5px}
.crow span{display:block;padding-left:28px}
.social{position:absolute;top:165px;width:14px;height:14px;border-radius:50%;background:var(--white)}
.map{position:absolute;left:758px;top:100px;width:312px;height:220px;background:linear-gradient(135deg,#3a3d44,#2c2f35 60%,#44474e)}
.footer .rule{position:absolute;left:0;top:400px;width:1200px;height:1px;background:#3a3f4c}
.footer .copy{position:absolute;left:0;top:416px;width:1200px;text-align:center;font-size:11px}
</style>
</head>
<body>

<header class="section topbar">
  <div class="brand" style="left:138px;top:21px"><span class="sq"></span>Lumora</div>
  <nav class="nav">
    <span style="left:0">HOME</span>
    <span style="left:93px">ABOUT</span>
    <span style="left:196px">OUR SERVICES</span>
    <span style="left:364px">OUR PROJECTS</span>
    <span style="left:536px">CONTACT</span>
  </nav>
</header>

<section class="section hero" role="img" aria-label="Engineer with laptop in a dimly lit server room aisle">
  <h1>IT Infrastructure | Smart Cabinet<br>| Micro Data Center</h1>
</section>

<section class="section services">
  <h2 class="heading" style="top:62px">OUR <span class="accent">SERVICES</span><span class="mark"></span></h2>
  <div class="svc" style="left:122px">
    <svg width="210" height="210"><circle cx="100" cy="100" r="93" fill="#fff" stroke="#e4e4e4" stroke-width="2"/><path d="M160 40 A88 88 0 0 1 116 190" fill="none" stroke="var(--navy)" stroke-width="7" stroke-linecap="round"/></svg>
    <div class="icon"></div>
    <div class="label">Data Center<br>Design and<br>Build</div>
  </div>
  <div class="svc" style="left:378px">
    <svg width="210" height="210"><circle cx="100" cy="100" r="93" fill="#fff" stroke="#e4e4e4" stroke-width="2"/><path d="M160 40 A88 88 0 0 1 116 190" fill="none" stroke="var(--navy)" stroke-width="7" stroke-linecap="round"/></svg>
    <div class="icon"></div>
    <div class="label">Structured<br>Cabling and<br>Fiber Backbone</div>
  </div>
  <div class="svc" style="left:644px">
    <svg width="210" height="210"><circle cx="100" cy="100" r="93" fill="#fff" stroke="#e4e4e4" stroke-width="2"/><path d="M160 40 A88 88 0 0 1 116 190" fill="none" stroke="var(--navy)" stroke-width="7" stroke-linecap="round"/></svg>
    <div class="icon"></div>
    <div class="label">Audiovisual<br>and Conference<br>Room</div>
  </div>
  <div class="svc" style="left:895px">
    <svg width="210" height="210"><circle cx="100" cy="100" r="93" fill="#fff" stroke="#e4e4e4" stroke-width="2"/><path d="M160 40 A88 88 0 0 1 116 190" fill="none" stroke="var(--navy)" stroke-width="7" stroke-linecap="round"/></svg>
    <div class="icon"></div>
    <div class="label">All-In-One<br>RAck / Micro-<br>Data Center</div>
  </div>
</section>

<section class="section about">
  <div class="photo" role="img" aria-label="Technician working on network equipment in a data center"></div>
  <h2>ABOUT LUMORA<br>SYSTEMS<span class="mark"></span></h2>
  <p>Lumora Systems is well experienced in delivering the best in Data Center Infrastructure, Network Infrastructure, Structured Cabling, Telephony, Access Control, Video Surveillance, Audiovisual &amp; Conferencing, Relocation &amp; Migration and Maintenance solutions.</p>
  <div class="btn-outline"><div class="back"></div><div class="front">READ MORE</div></div>
</section>

<section class="section projects">
  <h2 class="heading" style="top:76px">OUR <span class="accent">PROJECTS</span><span class="mark"></span></h2>
  <div class="proj" style="left:-6px"><div role="img" aria-label="Open server racks with patch cabling" style="width:263px;height:356px;background:linear-gradient(180deg,#3c434e,#1e242c 60%,#55606d)"></div><div class="cap">A renowned China based<br>listed insurance company</div></div>
  <div class="proj" style="left:312px"><div role="img" aria-label="Dense blue patch cables on a rack" style="width:263px;height:356px;background:linear-gradient(180deg,#2d5fa6,#1c3e78 50%,#3a78c4)"></div><div class="cap">Meridian Sourcing</div></div>
  <div class="proj" style="left:630px"><div role="img" aria-label="Black server cabinets on a tiled floor" style="width:263px;height:356px;background:linear-gradient(180deg,#e4e6ea,#2a2d33 45%,#c8cbd0)"></div><div class="cap">Halvern Capital<br>&amp; Ostrand Life</div></div>
  <div class="proj" style="left:948px"><div role="img" aria-label="Smart cabinet with display panel" style="width:263px;height:356px;background:linear-gradient(180deg,#d9dbde,#24272c 45%,#bfc2c6)"></div><div class="cap">A renowned China based<br>Securities firm</div></div>
</section>

<section class="section partners">
  <h2 class="heading light" style="top:46px">OUR PARTNERS<span class="mark"></span></h2>
  <div class="badge" style="left:135px;top:150px;width:145px"></div>
  <div class="badge" style="left:313px;top:150px;width:202px"></div>
  <div class="badge" style="left:550px;top:150px;width:148px"></div>
  <div class="badge" style="left:733px;top:150px;width:160px"></div>
  <div class="badge" style="left:925px;top:150px;width:138px"></div>
  <div class="badge" style="left:228px;top:252px;width:144px"></div>
  <div class="badge" style="left:428px;top:252px;width:165px"></div>
  <div class="badge" style="left:653px;top:252px;width:163px"></div>
  <div class="badge" style="left:880px;top:252px;width:92px"></div>
  <div class="dot" style="left:574px"></div>
  <div class="dot" style="left:592px;background:var(--red)"></div>
  <div class="dot" style="left:610px"></div>
</section>

<section class="section blog">
  <h2 class="heading" style="top:78px">OUR <span class="accent">BLOG</span><span class="mark"></span></h2>
  <article class="post" style="left:136px">
    <div class="img" role="img" aria-label="Engineer reviewing screens in a server room" style="background:linear-gradient(120deg,#0c2440,#1d5c8c 60%,#0a1a30)"></div>
    <div class="date">06,April,2023</div>
    <h3>Lorem Ipsum is simply dummy text of the printing and typesetting industry</h3>
    <div class="ex">Lorem Ipsum is simply dummy text of the printing and typesetting industry. Lorem Ipsum has been the industry's</div>
    <div class="more">READ MORE »</div>
  </article>
  <article class="post" style="left:460px">
    <div class="img" role="img" aria-label="Two colleagues checking a tablet beside server racks" style="background:linear-gradient(120deg,#14243e,#3b5f8a 55%,#0e1b30)"></div>
    <div class="date">08,Dec,2023</div>
    <h3>Lorem Ipsum is simply dummy text of the printing and typesetting industry</h3>
    <div class="ex">Lorem Ipsum is simply dummy text of the printing and typesetting industry. Lorem Ipsum has been the industry's</div>
    <div class="more">READ MORE »</div>
  </article>
  <article class="post" style="left:785px">
    <div class="img" role="img" aria-label="Technician with laptop in a data center" style="background:linear-gradient(120deg,#1c2532,#3e6fae 55%,#16202c)"></div>
    <div class="date">07,Feb,2023</div>
    <h3>Lorem Ipsum is simply dummy text of the printing and typesetting industry</h3>
    <div class="ex">Lorem Ipsum is simply dummy text of the printing and typesetting industry. Lorem Ipsum has been the industry's</div>
    <div class="more">READ MORE »</div>
  </article>
</section>

<section class="section events">
  <h2 class="heading light" style="top:32px">OUR EVENTS<span class="mark"></span></h2>
  <div class="tabs"><div>PREVIOUS EVENTS</div><div class="on">UPCOMING EVENTS</div></div>
  <div class="ev" style="top:246px"><div class="d">FEB<br>25</div><div class="t">Lorem ipsum dolor sit amet, consectetur adipiscing elit, sed do<br>eiusmod tempor incididunt</div></div>
  <div class="ev" style="top:316px"><div class="d">FEB<br>27</div><div class="t">Lorem ipsum dolor sit amet, consectetur adipiscing elit, sed do<br>eiusmod tempor incididunt</div></div>
  <div class="ev" style="top:386px"><div class="d">MAR<br>10</div><div class="t">Lorem ipsum dolor sit amet, consectetur adipiscing elit, sed do<br>eiusmod tempor incididunt</div></div>
  <div class="ev" style="top:454px"><div class="d">MAR<br>12</div><div class="t">Lorem ipsum dolor sit amet, consectetur adipiscing elit, sed do<br>eiusmod tempor incididunt</div></div>
  <div class="ev" style="top:522px"><div class="d">MAR<br>20</div><div class="t">Lorem ipsum dolor sit amet, consectetur adipiscing elit, sed do<br>eiusmod tempor incididunt</div></div>
  <div class="photo" role="img" aria-label="Glowing neon data center towers"></div>
</section>

<section class="section contact" role="img" aria-label="Server room corridor fading into the background">
  <h2 class="heading" style="top:82px">CONTACT <span class="accent">US</span><span class="mark"></span></h2>
  <div class="field" style="left:343px;top:178px">Name *</div>
  <div class="field" style="left:623px;top:178px">Email *</div>
  <div class="field" style="left:343px;top:255px">Phone *</div>
  <div class="field" style="left:623px;top:255px">Subject *</div>
  <div class="field" style="left:343px;top:326px;width:525px;height:98px">Message *</div>
  <div class="submit"><div class="back"></div><div class="front">SUBMIT</div></div>
</section>

<footer class="section footer">
  <div class="brand" style="left:122px;top:72px"><span class="sq"></span>Lumora</div>
  <div class="social" style="left:136px"></div>
  <div class="social" style="left:170px"></div>
  <h4 style="left:327px;top:44px">QUICK LINKS</h4>
  <div class="links">Home<br>About<br>Services<br>Projects<br>Contact Us</div>
  <h4 style="left:496px;top:44px">CONTACT US</h4>
  <div class="crow" style="top:82px">
    <svg width="14" height="14" viewBox="0 0 24 24"><path d="M5 3h4l2 5-3 2a12 12 0 0 0 6 6l2-3 5 2v4a2 2 0 0 1-2 2A18 18 0 0 1 3 5a2 2 0 0 1 2-2z" fill="none" stroke="#fff" stroke-width="1.8"/></svg>
    <span>+852 3100 4820 /<br>+852 6200 1947</span>
  </div>
  <div class="crow" style="top:152px;font-size:12px">
    <svg width="14" height="12" viewBox="0 0 24 20"><rect x="1" y="1" width="22" height="18" fill="none" stroke="#fff" stroke-width="1.8"/><path d="M1 1l11 9 11-9" fill="none" stroke="#fff" stroke-width="1.8"/></svg>
    <span>marketing@lumorasys.com.hk</span>
  </div>
  <div class="crow" style="top:200px">
    <svg width="14" height="16" viewBox="0 0 24 28"><path d="M12 26s9-9 9-15a9 9 0 0 0-18 0c0 6 9 15 9 15z" fill="none" stroke="#fff" stroke-width="1.8"/><circle cx="12" cy="11" r="3" fill="none" stroke="#fff" stroke-width="1.8"/></svg>
    <span>Rm 1208, 12/F, Harbourline<br>Centre, 18 Kestrel Street,<br>San Po Kong, Kowloon,<br>Hong Kong</span>
  </div>
  <div class="map" role="img" aria-label="Street map showing the office location in San Po Kong"></div>
  <div class="rule"></div>
  <div class="copy">© 2023 by Lumora Systems</div>
</footer>

</body>
</html>
```